Corvane Capital Business Cards

These are professional business cards that are for my family office.
Put fake emails and phone numbers as of now until I finalize those components. This family office controls my families investments, assets, and future. The cards should be professional.
..
.
.
.
I just uploaded another variation of a logo I would like to see as a business card to I am inbeteen which logo to use

Target Market(s)

business

Industry/Entity Type

business

Contact Information for Business Card

Professional, wealth related, finance related.

Requirements
Must have
• Logo

```html
<!DOCTYPE html>
<html lang="en">
<head>
<meta charset="utf-8">
<title>Corvane Capital Business Cards</title>
<link rel="stylesheet" href="https://fonts.googleapis.com/css2?family=Playfair+Display:wght@500&family=Poppins:wght@400;600;700&display=swap">
<style>
  :root {
    --bg: #1b1b1c;
    --card: #262627;
    --card-deep: #222223;
    --gold: #c8b27a;
    --cream: #f6f3df;
    --white: #f2f2f2;
    --grey: #a9a9ab;
    --grey-light: #d6d6d8;
  }
  * { box-sizing: border-box; margin: 0; padding: 0; }
  html, body { width: 1200px; height: 825px; overflow: hidden; background: var(--bg); }
  .canvas { position: relative; width: 1200px; height: 825px; }

  .card {
    position: absolute;
    width: 540px;
    height: 310px;
    background: var(--card);
    box-shadow: 0 14px 30px rgba(0,0,0,.45);
    overflow: hidden;
  }
  .card--front { left: 60px; top: 140px; }
  .card--back { left: 600px; top: 380px; background: var(--card-deep); }

  .wordmark {
    font-family: "Playfair Display", serif;
    font-weight: 500;
    color: var(--white);
    letter-spacing: .08em;
    text-transform: uppercase;
    display: flex;
    align-items: center;
    gap: 14px;
    white-space: nowrap;
  }
  .wordmark__square { background: var(--gold); flex: none; }

  .card--front .wordmark {
    position: absolute; left: 0; right: 0; top: 0; bottom: 0;
    justify-content: center;
    font-size: 38px;
  }
  .card--front .wordmark__square { width: 26px; height: 26px; }

  .back__brand {
    position: absolute; left: 0; top: 0; width: 212px; height: 310px;
  }
  .back__tab {
    position: absolute; left: 0; top: 168px; width: 40px; height: 128px;
    background: var(--gold); border-radius: 0 8px 8px 0;
  }
  .back__brand .wordmark {
    position: absolute; left: 48px; right: 12px; top: 140px;
    justify-content: center;
    font-size: 12px; gap: 6px; letter-spacing: .06em;
  }
  .back__brand .wordmark__square { width: 9px; height: 9px; }

  .back__stripe {
    position: absolute; left: 212px; top: 0; width: 20px; height: 310px;
    background: linear-gradient(180deg, var(--cream) 0%, var(--cream) 55%, var(--gold) 100%);
  }

  .back__info { position: absolute; left: 258px; top: 26px; right: 20px; font-family: "Poppins", sans-serif; }
  .back__edge { position: absolute; right: 22px; top: 0; width: 3px; height: 40px; background: var(--grey-light); }

  .person__name { font-weight: 700; font-size: 23px; color: var(--grey); letter-spacing: .04em; text-transform: uppercase; }
  .person__role { display: flex; align-items: center; gap: 10px; margin-top: 4px; }
  .person__dash { width: 22px; height: 2px; background: var(--grey-light); }
  .person__title { background: var(--grey-light); font-size: 11px; font-weight: 600; padding: 2px 14px; color: #f7f7f7; text-shadow: 0 0 1px rgba(0,0,0,.15); }

  .contacts { list-style: none; margin-top: 30px; display: grid; gap: 10px; }
  .contact { display: flex; align-items: center; gap: 10px; }
  .contact__icon {
    width: 26px; height: 26px; flex: none;
    background: var(--grey); display: flex; align-items: center; justify-content: center;
  }
  .contact__icon svg { width: 15px; height: 15px; }
  .contact__label { font-size: 10.5px; line-height: 1.25; color: var(--grey-light); }
  .contact__value { font-size: 11px; line-height: 1.25; color: var(--grey-light); }
</style>
</head>
<body>
<main class="canvas">

  <section class="card card--front" aria-label="Card front">
    <div class="wordmark"><span class="wordmark__square"></span>Corvane Capital</div>
  </section>

  <section class="card card--back" aria-label="Card back">
    <div class="back__brand">
      <div class="back__tab"></div>
      <div class="wordmark"><span class="wordmark__square"></span>Corvane Capital</div>
    </div>

    <div class="back__stripe"></div>
    <div class="back__edge"></div>

    <div class="back__info">
      <h1 class="person__name">Elliot Marrow</h1>
      <div class="person__role">
        <span class="person__dash"></span>
        <span class="person__title">Founder &amp; Chairman</span>
      </div>

      <ul class="contacts">
        <li class="contact">
          <span class="contact__icon">
            <svg viewBox="0 0 24 24" fill="none" stroke="#fff" stroke-width="2" stroke-linecap="round" stroke-linejoin="round"><path d="M5 3h4l2 5-3 2a11 11 0 0 0 6 6l2-3 5 2v4a2 2 0 0 1-2 2A17 17 0 0 1 3 5a2 2 0 0 1 2-2z"/></svg>
          </span>
          <div><p class="contact__label">Phone :</p><p class="contact__value">+123 456 7890</p></div>
        </li>
        <li class="contact">
          <span class="contact__icon">
            <svg viewBox="0 0 24 24" fill="#fff"><path d="M2 11 22 3l-5 18-5-7-6 3 2-5z"/></svg>
          </span>
          <div><p class="contact__label">Email :</p><p class="contact__value">info@corvanecapital.com</p></div>
        </li>
        <li class="contact">
          <span class="contact__icon">
            <svg viewBox="0 0 24 24" fill="none" stroke="#fff" stroke-width="1.8"><circle cx="12" cy="12" r="9"/><path d="M3 12h18M12 3c3 3 3 15 0 18M12 3c-3 3-3 15 0 18"/></svg>
          </span>
          <div><p class="contact__label">Website :</p><p class="contact__value">www.corvanecapital.com</p></div>
        </li>
        <li class="contact">
          <span class="contact__icon">
            <svg viewBox="0 0 24 24" fill="#fff"><path d="M12 2a7 7 0 0 0-7 7c0 5 7 13 7 13s7-8 7-13a7 7 0 0 0-7-7zm0 9.5A2.5 2.5 0 1 1 12 6.5a2.5 2.5 0 0 1 0 5z"/></svg>
          </span>
          <div><p class="contact__label">Location :</p><p class="contact__value">123, Your Street,<br>Zipo Code, Country</p></div>
        </li>
      </ul>
    </div>
  </section>

</main>
</body>
</html>
```